Landing Page and Logo for Auto-Blogging Platform

I created a platform that allows users to start a blog for their business, hobby, charity, etc. I need a landing page where users can learn about the platform, benefits of consistent blogging, SEO value, plans/pricing, etc. The landing page needs to have multiple call to action buttons encouraging the visitor to register/sign up for a free trial.

In addition to the landing page, I need a page for users to establish the settings for their blog. This page should be a fairly simple form, intended for the user to enter a few details to set up their blog:
1. Name of Blog
2. Up to 10 topics and/or keywords the blog should focus on
3. Theme: Color-scheme and logo upload for blog.

I have attached the specifications of the platform's functionality so you can better understand how it works, plans/pricing, etc.

I also need a logo for the business. The name of the platform is PostNook.

Target Market(s)

Website owners, bloggers, business owners

Industry/Entity Type

Technology, Internet, web design

Coding

Coded - Design and coding required

Number of Pages Required

2 page

Colors
0054AA
0677BA
7BADD7
CADEEF
E8F1F8
0094D4
00A9DD
6FCCEA
C7EBF8
E9F6FB

Requirements
Must have
• Eye-catching design but fairly light on content (keep it simple and brief.)
Nice to have
• Eye-catching yet simple design, clean and easy to understand what we are offering.
Should not have
• Too much “wordy” and confusing content.

```html
<!DOCTYPE html>
<html lang="en">
<head>
<meta charset="utf-8">
<title>PostNook – Automate Your Blog Posting with AI</title>
<link href="https://fonts.googleapis.com/css2?family=Poppins:wght@600;700;800&family=Roboto:wght@400;500;700&display=swap" rel="stylesheet">
<style>
:root{
  --blue:#0054AA;
  --blue-mid:#0677BA;
  --blue-soft:#7BADD7;
  --blue-pale:#CADEEF;
  --blue-wash:#E8F1F8;
  --cyan:#0094D4;
  --cyan-bright:#00A9DD;
  --cyan-soft:#6FCCEA;
  --cyan-pale:#C7EBF8;
  --text:#333a44;
  --muted:#555d68;
  --white:#ffffff;
  --orange:#E0952A;
}
*{margin:0;padding:0;box-sizing:border-box}
html,body{width:1200px;height:2933px;overflow:hidden;background:var(--white)}
body{position:relative;font-family:'Roboto',Arial,sans-serif;color:var(--text)}
.abs{position:absolute}
.heading{font-family:'Poppins',Arial,sans-serif;font-weight:800;color:var(--blue);letter-spacing:-.3px}
.btn{position:absolute;display:flex;align-items:center;justify-content:center;border-radius:24px;color:var(--white);font-weight:700;font-size:13px;text-transform:uppercase;letter-spacing:-.2px;background:var(--blue)}

/* header */
.site-header{position:absolute;left:0;top:0;width:1200px;height:85px;border-top:4px solid var(--blue);background:var(--white);border-bottom:1px solid #e3e7ec}
.brand{position:absolute;left:145px;top:12px;display:flex;align-items:center;gap:8px}
.brand-dot{width:52px;height:52px;border-radius:50%;background:var(--blue-mid)}
.brand-name{font-family:'Poppins',sans-serif;font-weight:700;font-size:40px;color:var(--blue);line-height:1}
.nav a{position:absolute;top:38px;font-size:14px;color:#222;text-decoration:none;font-weight:500}
.nav .active::after{content:"";position:absolute;right:-12px;top:6px;width:7px;height:7px;border-radius:50%;background:var(--cyan)}

/* hero */
.hero-photo{position:absolute;left:0;top:85px;width:1200px;height:516px;background:linear-gradient(110deg,#6b4a33 0%,#8a6444 35%,#4e4f55 60%,#2f3238 80%,#c8c2b8 100%)}
.hero-panel{position:absolute;left:145px;top:156px;width:466px;height:369px;background:var(--blue);border-top-left-radius:70px;padding:26px 45px}
.hero-title{font-family:'Poppins',sans-serif;font-weight:800;font-size:41px;line-height:43px;color:var(--white)}
.hero-text{margin-top:22px;font-size:14.5px;line-height:21.6px;color:var(--white);text-align:justify}
.slider-dot{position:absolute;left:57px;width:8px;height:8px;border-radius:50%;background:var(--white)}

/* how it works */
.mountain-soft{position:absolute;left:0;width:1200px}
.section-title{position:absolute;left:0;width:1200px;text-align:center;font-size:44px}
.underline{position:absolute;height:4px;width:48px;background:var(--cyan);border-radius:2px}
.step{position:absolute;top:866px;width:200px;text-align:center}
.step svg{display:block;margin:0 auto}
.step p{margin-top:18px;font-size:16.5px;line-height:20px;color:#222}
.body-copy{font-size:14.5px;line-height:24.8px;color:var(--muted)}
.about-copy{font-size:14px;line-height:24.8px;letter-spacing:-.15px;color:var(--muted)}

/* about */
.about-panel{position:absolute;left:55px;top:1395px;width:1145px;height:628px;background:var(--blue-wash);border-top-left-radius:80px}
.about-media{position:absolute;left:142px;top:1471px;width:321px;height:476px;background:var(--white);padding:22px}
.about-media .fill{width:100%;height:100%;background:linear-gradient(160deg,#2c3f63 0%,#9aa8b8 40%,#d7dbe0 65%,#7a6f66 100%)}

/* pricing */
.plan{position:absolute;top:2214px;height:232px;background:var(--white);border:2px solid #dfe3e8;border-top-left-radius:60px;text-align:center}
.plan.featured{background:#f5f8fc;box-shadow:0 6px 16px rgba(0,60,120,.12)}
.plan h3{margin-top:38px;font-size:23px;font-weight:500;color:var(--blue)}
.plan .desc{margin-top:12px;font-size:15.5px;line-height:20px;color:#333}
.plan .price{margin-top:12px;font-size:22px;font-weight:700;color:var(--cyan)}
.plan .btn{position:static;margin:14px auto 0;width:108px;height:40px;font-size:11.5px}

/* footer */
.site-footer{position:absolute;left:0;top:2683px;width:1200px;height:250px;background:var(--blue);color:var(--white)}
.contact{position:absolute;top:48px;display:flex;align-items:center;gap:18px}
.contact .ic{width:52px;height:52px;border-radius:50%;background:var(--white);display:flex;align-items:center;justify-content:center}
.contact strong{display:block;font-size:17px;font-weight:500}
.contact span{font-size:15px}
.legal{position:absolute;top:142px;left:0;width:1200px;text-align:center;font-size:13.5px}
.social{position:absolute;top:182px;left:544px;display:flex;gap:12px}
.social span{width:29px;height:29px;border-radius:50%;background:var(--white)}
</style>
</head>
<body>

<header class="site-header">
  <div class="brand"><span class="brand-dot"></span><span class="brand-name">PostNook</span></div>
  <nav class="nav">
    <a class="active" style="left:461px">HOME</a>
    <a style="left:535px">PRICING</a>
    <a style="left:623px">HOW IT WORKS</a>
    <a style="left:758px">CONTACT</a>
  </nav>
  <a class="btn" style="left:856px;top:21px;width:197px;height:42px">Sign up for a free trial</a>
</header>

<section>
  <div class="hero-photo" role="img" aria-label="Photo of a person typing a blog post on a laptop at a wooden desk with coffee, notebooks and pencils"></div>
  <div class="hero-panel">
    <h1 class="hero-title">Automate Your<br>Blog Posting<br>with AI</h1>
    <p class="hero-text">Transform your blogging experience with our AI-powered platform that not only generates and optimizes content tailored to your audience but also continuously learns and adapts to deliver smarter insights, ensuring your voice stands out in a crowded digital landscape.</p>
  </div>
  <a class="btn" style="left:190px;top:453px;width:197px;height:42px;background:var(--blue-soft)">Sign up for a free trial</a>
  <span class="slider-dot" style="top:506px"></span>
  <span class="slider-dot" style="top:521px"></span>
  <span class="slider-dot" style="top:535px;width:12px;height:12px;left:55px;background:var(--blue-soft);border:2px solid var(--white)"></span>
</section>

<section>
  <div class="mountain-soft" style="top:930px;height:430px;background:linear-gradient(180deg,#ffffff 0%,#eef1f4 45%,#e2e7ec 80%,#ffffff 100%)" role="img" aria-label="Faint misty mountain peak in the background"></div>
  <h2 class="heading section-title" style="top:678px">How It Works</h2>
  <p class="abs" style="left:0;top:752px;width:1200px;text-align:center;font-size:17.5px;color:#333">The blog topics can be created using any of these methods</p>
  <div class="underline" style="left:576px;top:792px"></div>

  <div class="step" style="left:175px">
    <svg width="170" height="130" viewBox="0 0 170 130">
      <text x="8" y="105" font-family="Poppins,sans-serif" font-size="110" font-weight="600" fill="#fff" stroke="#0054AA" stroke-width="3">1</text>
      <circle cx="100" cy="64" r="60" fill="#fff" stroke="#0054AA" stroke-width="3"/>
      <circle cx="54" cy="24" r="6" fill="#7BADD7"/>
      <circle cx="100" cy="64" r="45" fill="#0054AA"/>
      <rect x="84" y="52" width="32" height="28" rx="3" fill="#fff"/>
      <rect x="90" y="46" width="4" height="10" rx="2" fill="#fff"/><rect x="106" y="46" width="4" height="10" rx="2" fill="#fff"/>
      <rect x="84" y="60" width="32" height="2" fill="#0054AA"/>
    </svg>
    <p>Select frequency<br>of Automated Blog Posts<br>(daily, weekly, or monthly)</p>
  </div>
  <div class="step" style="left:407px">
    <svg width="170" height="130" viewBox="0 0 170 130">
      <text x="0" y="105" font-family="Poppins,sans-serif" font-size="110" font-weight="600" fill="#fff" stroke="#0054AA" stroke-width="3">2</text>
      <circle cx="104" cy="64" r="60" fill="#fff" stroke="#0054AA" stroke-width="3"/>
      <circle cx="58" cy="24" r="6" fill="#7BADD7"/>
      <path d="M90 84 L94 66 L118 42 L126 50 L102 74 Z" fill="#0054AA"/>
      <rect x="88" y="88" width="34" height="4" rx="2" fill="#0054AA"/>
    </svg>
    <p>Name your<br>blog Step</p>
  </div>
  <div class="step" style="left:642px">
    <svg width="170" height="130" viewBox="0 0 170 130">
      <text x="0" y="105" font-family="Poppins,sans-serif" font-size="110" font-weight="600" fill="#fff" stroke="#0054AA" stroke-width="3">3</text>
      <circle cx="104" cy="64" r="60" fill="#fff" stroke="#0054AA" stroke-width="3"/>
      <circle cx="58" cy="24" r="6" fill="#7BADD7"/>
      <path d="M88 42 H112 L122 52 V88 H88 Z" fill="#0054AA"/>
      <path d="M112 42 V52 H122" fill="#7BADD7"/>
    </svg>
    <p>Select your blog<br>topics (or let AI<br>choose them<br>for you)</p>
  </div>
  <div class="step" style="left:877px">
    <svg width="180" height="130" viewBox="0 0 180 130">
      <text x="0" y="105" font-family="Poppins,sans-serif" font-size="110" font-weight="600" fill="#fff" stroke="#0054AA" stroke-width="3">4</text>
      <circle cx="110" cy="64" r="60" fill="#fff" stroke="#0054AA" stroke-width="3"/>
      <circle cx="64" cy="24" r="6" fill="#7BADD7"/>
      <rect x="103" y="44" width="14" height="12" fill="#0054AA"/>
      <path d="M110 56 V64 M92 64 H128 M92 64 V72 M110 64 V72 M128 64 V72" stroke="#0054AA" stroke-width="3" fill="none"/>
      <rect x="85" y="72" width="14" height="12" fill="#0054AA"/><rect x="103" y="72" width="14" height="12" fill="#0054AA"/><rect x="121" y="72" width="14" height="12" fill="#0054AA"/>
    </svg>
    <p>Go do something<br>else and let AI do all<br>your blogging for<br>you!</p>
  </div>

  <p class="abs body-copy" style="left:198px;top:1139px;width:804px;text-align:center">There should also be an option for the user to generate a blog post instantly (outside of&nbsp; their regularly-scheduled auto-posts) if they are on the Ultimate Plan. I will choose a domain name for the platform. Each user will receive a subdomain (such as craftytools.nookhost.net) or a path from the root domain (such as&nbsp; nookhost.net/craftytools). The subdomain would be preferred, but the path option&nbsp; would also be acceptable, if necessary</p>
  <a class="btn" style="left:496px;top:1269px;width:208px;height:43px">Sign up for a free trial</a>
</section>

<section>
  <div class="about-panel"></div>
  <div class="about-media"><div class="fill" role="img" aria-label="Collage of sample blog layouts and an email newsletter with mountain and landscape photos"></div></div>
  <h2 class="heading abs" style="left:537px;top:1462px;font-size:46px;line-height:58px">About<br>The Platform</h2>
  <div class="underline" style="left:537px;top:1577px"></div>
  <p class="abs about-copy" style="left:537px;top:1604px;width:516px;text-align:justify">There needs to be a super-admin panel where platform owner/administrator can see&nbsp; users, their activity, manage user access, etc.Each user will have a dashboard where they control their settings such as account information, billing, view blog posts, view blog post topics, etc. From this dashboard, the user can customize the “look and feel” of their blog including theme, hero banner, header, footer, logo, color scheme, etc.The platform will require a list of blog topics. Based on the topics list, the software will need to automatically send prompts to TextForge in the specified intervals (monthly, weekly, or daily), receive the blog content, and post it to the blog. Furthermore, the software will need some method of adding at least one image to each blog post. Ideally, this would be achieved by using the PicVault API to retrieve image(s) based on keywords in the blog topic</p>
  <a class="btn" style="left:537px;top:1901px;width:119px;height:42px">Read more</a>
</section>

<section>
  <h2 class="heading abs" style="left:146px;top:2082px;font-size:46px">Pricing Plan</h2>
  <div class="underline" style="left:146px;top:2149px"></div>
  <p class="abs body-copy" style="left:511px;top:2094px;width:540px;line-height:25px">SAAS model. The platform can be used to sell unique accounts to multiple users. There must be a subscription plan and a 14-day free trial. The subscriptions are:</p>
  <div class="mountain-soft" style="top:2330px;height:353px;background:linear-gradient(180deg,#f4f6f8 0%,#c9d1da 45%,#8e9aa8 70%,#dfe4ea 100%)" role="img" aria-label="Snow-covered mountain range under a pale sky"></div>

  <div class="plan" style="left:143px;width:296px">
    <h3>Base Plan</h3>
    <p class="desc">1 blog post (up to 2,000 words)<br>every month</p>
    <p class="price">$9.99/mo</p>
    <a class="btn">View plan</a>
  </div>
  <div class="plan featured" style="left:452px;width:296px">
    <h3>Premium Plan</h3>
    <p class="desc">1 blog post (up to 2,000 words)<br>every week</p>
    <p class="price">$14.99/mo</p>
    <a class="btn" style="background:var(--cyan)">View plan</a>
  </div>
  <div class="plan" style="left:760px;width:297px">
    <h3>Ultimate Plan</h3>
    <p class="desc">1 blog post (up to 3,000 words) per day<br>plus unlimited manual posting</p>
    <p class="price">$24.99/mo</p>
    <a class="btn">View plan</a>
  </div>
</section>

<footer class="site-footer">
  <div class="contact" style="left:211px">
    <span class="ic"><svg width="22" height="26" viewBox="0 0 22 26"><path d="M11 1C5.5 1 1.5 5 1.5 10.2 1.5 17 11 25 11 25S20.5 17 20.5 10.2C20.5 5 16.5 1 11 1Z" fill="#0054AA"/><circle cx="11" cy="10" r="3.6" fill="#fff"/></svg></span>
    <div><strong>Location</strong><span>48 Larkspur Lane</span></div>
  </div>
  <div class="contact" style="left:520px">
    <span class="ic" style="background:var(--orange)"><svg width="26" height="18" viewBox="0 0 26 18"><rect x="1" y="1" width="24" height="16" rx="2" fill="#fff"/><path d="M1 2 L13 10 L25 2" stroke="#E0952A" stroke-width="2" fill="none"/></svg></span>
    <div><strong>Email</strong><span>hello@postnook-mail.com</span></div>
  </div>
  <div class="contact" style="left:804px">
    <span class="ic"><svg width="24" height="24" viewBox="0 0 24 24"><path d="M5 2 L9 2 L11 7 L8.5 9 C9.8 12 12 14.2 15 15.5 L17 13 L22 15 L22 19 C22 20.5 20.5 22 19 22 C10 21.5 2.5 14 2 5 C2 3.5 3.5 2 5 2Z" fill="#0054AA"/></svg></span>
    <div><strong>CALL US</strong><span>+1 555 014 2290</span></div>
  </div>
  <p class="legal">© 2024 PostNook – All Rights Reserved &nbsp;|&nbsp; Privacy&nbsp; Policy &nbsp;|&nbsp; Terms of Use</p>
  <div class="social" aria-label="Social links"><span></span><span></span><span></span></div>
</footer>

</body>
</html>
```